Corporate Business Card

Very professional, Modern, Not to busy, include phone address email, website
(253) 617-4930, 18761 52nd Avenue S, Kent, WA 98047, martin@plumlinegroup.com, varkoworks.com

Target Market(s)

Manufacturing

Industry/Entity Type

Aero, machining, manufacturing, Off road racing

Contact Information for Business Card

Phone, address email, website

```html
<!DOCTYPE html>
<html lang="en">
<head>
<meta charset="utf-8">
<title>Varko Works – Business Card</title>
<link rel="stylesheet" href="https://fonts.googleapis.com/css2?family=Saira:wght@700&family=Roboto:wght@400&display=swap">
<style>
  :root {
    --backdrop: #2b2b2b;
    --navy: #2c3a6a;
    --navy-deep: #263361;
    --red: #bf2228;
    --white: #f2f2f2;
    --card-radius: 14px;
  }
  html, body {
    margin: 0;
    padding: 0;
    width: 1200px;
    height: 1138px;
    overflow: hidden;
    background: var(--backdrop);
  }
  .canvas {
    position: relative;
    width: 1200px;
    height: 1138px;
  }
  .card {
    position: absolute;
    left: 275px;
    width: 620px;
    height: 375px;
    border-radius: var(--card-radius);
    background: var(--navy);
    overflow: hidden;
  }
  .card--front { top: 186px; }
  .card--back  { top: 608px; background: linear-gradient(180deg, var(--navy) 0%, var(--navy-deep) 100%); }

  .front-pattern {
    position: absolute;
    inset: 0;
    background: linear-gradient(160deg, #33417a 0%, #2a3768 55%, #222d58 100%);
  }
  .front-name {
    position: absolute;
    left: 52px;
    top: 288px;
    font-family: "Saira", sans-serif;
    font-weight: 700;
    font-size: 38px;
    line-height: 1;
    color: var(--white);
    letter-spacing: 1px;
  }

  .person-name {
    position: absolute;
    left: 27px;
    top: 80px;
    margin: 0;
    font-family: "Saira", sans-serif;
    font-weight: 700;
    font-size: 25px;
    line-height: 1;
    letter-spacing: 0.5px;
    color: var(--white);
  }
  .person-name .surname { color: var(--red); }

  .contact-band {
    position: absolute;
    left: 0;
    top: 138px;
    width: 302px;
    height: 99px;
    background: var(--red);
  }
  .contact-list {
    list-style: none;
    margin: 0;
    padding: 13px 0 0 0;
  }
  .contact-list li {
    display: flex;
    align-items: center;
    height: 24.5px;
    font-family: "Roboto", sans-serif;
    font-size: 16px;
    color: var(--white);
  }
  .contact-list svg {
    width: 14px;
    height: 14px;
    margin: 0 18px 0 27px;
    fill: var(--white);
    flex: none;
  }
  .accent-bar {
    position: absolute;
    left: 610px;
    top: 138px;
    width: 10px;
    height: 99px;
    background: var(--red);
  }
  .company-name {
    position: absolute;
    left: 318px;
    top: 160px;
    width: 276px;
    text-align: center;
    font-family: "Saira", sans-serif;
    font-weight: 700;
    font-size: 36px;
    line-height: 56px;
    color: var(--white);
    letter-spacing: 1px;
  }
  .address {
    position: absolute;
    left: 27px;
    top: 256px;
    margin: 0;
    font-family: "Roboto", sans-serif;
    font-style: normal;
    font-size: 16.5px;
    line-height: 25px;
    color: var(--white);
  }
</style>
</head>
<body>
<main class="canvas">
  <section class="card card--front" aria-label="Card front">
    <div class="front-pattern" role="img" aria-label="Tonal embossed repeat of the company mark across the navy card face"></div>
    <div class="front-name">VARKO WORKS</div>
  </section>

  <section class="card card--back" aria-label="Card back">
    <h1 class="person-name">MARTIN <span class="surname">HALE</span></h1>

    <div class="contact-band">
      <ul class="contact-list">
        <li>
          <svg viewBox="0 0 16 16" aria-hidden="true"><path d="M3 6c0-2 2-3 5-3s5 1 5 3v1h-3V6H6v1H3zM4 8h8l2 5H2z"/></svg>
          (253) 617-4930
        </li>
        <li>
          <svg viewBox="0 0 16 16" aria-hidden="true"><path d="M1 3h14v10H1zM2.5 4.5v.4L8 9l5.5-4.1v-.4zM2.5 6.6v5h11v-5L8 10.7z"/></svg>
          martin@plumlinegroup.com
        </li>
        <li>
          <svg viewBox="0 0 16 16" aria-hidden="true"><path d="M8 1a7 7 0 1 0 0 14A7 7 0 0 0 8 1zm0 1.5c.8 0 1.7 1.6 1.9 4.5H6.1C6.3 4.1 7.2 2.5 8 2.5zM2.6 7h2.2c.1-1.6.4-3 .9-3.9A5.5 5.5 0 0 0 2.6 7zm8.6 0h2.2a5.5 5.5 0 0 0-3.1-3.9c.5.9.8 2.3.9 3.9zM2.6 9a5.5 5.5 0 0 0 3.1 3.9c-.5-.9-.8-2.3-.9-3.9zm3.5 0c.2 2.9 1.1 4.5 1.9 4.5s1.7-1.6 1.9-4.5zm5.1 0c-.1 1.6-.4 3-.9 3.9A5.5 5.5 0 0 0 13.4 9z"/></svg>
          www.varkoworks.com
        </li>
      </ul>
    </div>

    <div class="company-name">VARKO WORKS</div>
    <div class="accent-bar"></div>

    <address class="address">18761 52nd Avenue S,<br>Kent, WA 98047</address>
  </section>
</main>
</body>
</html>
```